Commercial/Retail/Office Real Estate Lease Brochure for Vacant Space

We need a commercial Real Estate Fyler Template for lease space. We would like it for Vacant lease spaces and new buildings in the commercial, retail, office and industrial lease space. The flyer should have sections for: Highlights (site size, leasable area, Location, Ammenties etc.), concept floor plan or site plan, contact information, project/construction description.

Target Market(s)

Commercial Leasing for Offices and Retail Space

Industry/Entity Type

Real Estate Leasing and Development

Requirements
Must have
• Clean, timeless not overly busy template with spots for key metrics (square feet leaseable space, parking etc), location for pictures
Nice to have
• Marlow Crest Real Estate Logo for header/foot, reusable with adjustments for other spaces
Should not have
• Busy, overall colorfull or contrasting

```html
<!DOCTYPE html>
<html lang="en">
<head>
<meta charset="utf-8">
<title>Commercial Leasing Opportunity – Ref. 5009</title>
<link href="https://fonts.googleapis.com/css2?family=PT+Sans:wght@400;700&family=Roboto+Condensed:wght@300;400;700&display=swap" rel="stylesheet">
<style>
  :root{
    --stage:#eef1f5;
    --white:#ffffff;
    --navy:#1f3a66;
    --navy-panel:rgba(31,58,102,.88);
    --navy-deep:#243f6c;
    --blue:#1d5ca8;
    --ink:#3a3f47;
    --muted:#8b96a6;
    --rule:#c9d1dc;
    --photo-sky:#a9c2dc;
    --photo-brick:#8a5a45;
    --photo-night:#2a3550;
    --plan:#e6e9ee;
    --map:#dfe8ef;
  }
  *{margin:0;padding:0;box-sizing:border-box}
  html,body{width:1200px;height:2492px;overflow:hidden}
  body{background:var(--stage);font-family:"PT Sans",Arial,sans-serif;color:var(--ink);position:relative}
  .abs{position:absolute}
  .photo-day{background:linear-gradient(180deg,var(--photo-sky) 0%,#c7d6e6 45%,var(--photo-brick) 46%,#6e5246 80%,#6b6f70 100%)}
  .photo-night{background:linear-gradient(180deg,var(--photo-night) 0%,#3c4a6a 40%,#8a6a46 60%,#4a4a4a 100%)}
  .photo-brick{background:linear-gradient(180deg,#b6cde3 0%,#c9d8e7 40%,#9a6550 42%,#7a5243 85%,#707474 100%)}

  /* ---------- miniature sheets ---------- */
  .sheet{position:absolute;top:112px;width:330px;height:568px;background:var(--white);overflow:hidden}
  .sheet-back{left:120px}
  .sheet-front{left:750px}
  .mini-title{position:absolute;left:20px;font-family:"Roboto Condensed",sans-serif;color:var(--blue);font-size:22px}
  .mini-plan{left:20px;top:54px;width:290px;height:230px;background:var(--plan);border:1px solid var(--rule)}
  .mini-text{position:absolute;font-size:10px;line-height:14px;color:var(--ink)}
  .mini-map{left:170px;top:350px;width:140px;height:140px;background:var(--map)}
  .mini-foot{left:0;bottom:0;width:100%;height:50px;background:var(--blue);color:var(--white);display:flex;align-items:center;padding:0 20px;gap:40px}
  .mini-foot b{font-family:"Roboto Condensed",sans-serif;font-weight:400;font-size:18px}
  .mini-foot span{font-size:8px;line-height:11px}
  .mini-col{right:0;top:30px;width:105px;height:488px;background:var(--navy-deep)}
  .mini-head{left:18px;top:10px;font-size:10px}
  .mini-hero{left:0;top:52px;width:225px;height:150px}
  .mini-headline{left:234px;top:80px;color:var(--white);font-family:"Roboto Condensed",sans-serif;font-size:18px;line-height:20px}
  .mini-metric{left:234px;color:var(--white);font-size:9px;line-height:12px}

  /* ---------- flyer ---------- */
  .flyer{position:absolute;left:0;top:820px;width:1200px;height:1672px;background:var(--white);overflow:hidden}
  .side-column{position:absolute;left:820px;top:92px;width:380px;height:1448px;background:var(--navy-deep)}
  .logo-slot{position:absolute;left:48px;top:112px;font-family:"PT Sans",sans-serif;font-size:30px;color:#222}
  .phone-icon{position:absolute;left:748px;top:114px}
  .ref-tag{position:absolute;left:852px;top:112px;font-size:30px;color:var(--white)}
  .hero{position:absolute;left:0;top:188px;width:1200px;height:572px}
  .hero-panel{position:absolute;left:820px;top:188px;width:380px;height:572px;background:var(--navy-panel)}
  .headline{position:absolute;left:844px;top:436px;font-family:"Roboto Condensed",sans-serif;font-weight:300;font-size:76px;line-height:80px;color:var(--white)}
  .section-title{position:absolute;left:48px;top:794px;font-family:"Roboto Condensed",sans-serif;font-weight:300;font-size:64px;color:var(--navy)}
  .highlights{position:absolute;top:900px;list-style:none;font-size:22px;line-height:27px;color:var(--muted)}
  .highlights li::before{content:"";display:inline-block;width:8px;height:8px;border-radius:50%;background:var(--rule);margin-right:16px;vertical-align:middle}
  .col-a{left:48px}
  .col-b{left:440px}
  .metric{position:absolute;left:852px;color:var(--white)}
  .metric-icon{position:absolute;left:0;top:4px;opacity:.35}
  .metric-label{position:absolute;left:60px;top:0;font-size:15px;letter-spacing:1px;opacity:.55;white-space:nowrap}
  .metric-value{position:absolute;left:60px;top:18px;font-family:"Roboto Condensed",sans-serif;font-size:44px;white-space:nowrap}
  .gallery-main{position:absolute;left:0;top:1200px;width:792px;height:320px}
  .gallery-side{position:absolute;left:820px;width:380px;height:160px}
  .contact-band{position:absolute;left:0;top:1540px;width:1200px;height:132px;background:var(--blue);color:var(--white)}
  .contact-title{position:absolute;left:48px;top:34px;font-family:"Roboto Condensed",sans-serif;font-weight:300;font-size:60px}
  .contact-card{position:absolute;left:352px;top:38px;font-size:16px;line-height:20px}
  .contact-card strong{font-weight:700}
</style>
</head>
<body>

  <!-- miniature back sheet -->
  <section class="sheet sheet-back">
    <h2 class="mini-title" style="top:16px">Site Plan</h2>
    <div class="abs mini-plan" role="img" aria-label="Concept floor plan of the lease space"></div>
    <h2 class="mini-title" style="top:300px">Project Description</h2>
    <p class="mini-text" style="left:20px;top:340px;width:140px">Modern two-storey office building with flexible suites, open floor plates and ample parking near main routes.</p>
    <div class="abs mini-map" role="img" aria-label="Location map of the site"></div>
    <footer class="abs mini-foot"><b>Contact Us</b><span>Daniel Ashford<br>Vice President</span></footer>
  </section>

  <!-- miniature front sheet -->
  <section class="sheet sheet-front">
    <div class="abs mini-col"></div>
    <div class="abs mini-head">Logo here</div>
    <div class="abs mini-text" style="left:234px;top:36px;color:#fff">Ref. 5009</div>
    <div class="abs mini-hero photo-brick" role="img" aria-label="Two-storey brick office building"></div>
    <div class="abs mini-headline">Commercial<br>Leasing<br>Opportunity</div>
    <h2 class="mini-title" style="top:214px;color:var(--navy)">Highlights</h2>
    <p class="mini-text" style="left:20px;top:250px;width:200px;color:var(--muted)">Close to transit<br>Flexible suites<br>New construction<br>Ample parking</p>
    <div class="abs mini-metric" style="top:250px">SITE SIZE<br>2260 SF</div>
    <div class="abs mini-metric" style="top:290px">LEASABLE AREA<br>960 SF</div>
    <div class="abs mini-metric" style="top:330px">PRIVATE<br>PARKING</div>
    <div class="abs photo-night" style="left:0;top:380px;width:225px;height:130px" role="img" aria-label="Office building at dusk"></div>
    <footer class="abs mini-foot"><b>Contact Us</b></footer>
  </section>

  <!-- flyer front page -->
  <article class="flyer">
    <div class="side-column"></div>
    <div class="logo-slot">Logo here</div>
    <svg class="phone-icon" width="40" height="40" viewBox="0 0 24 24" aria-hidden="true">
      <path d="M6.6 10.8a15 15 0 0 0 6.6 6.6l2.2-2.2a1 1 0 0 1 1-.25 11.4 11.4 0 0 0 3.6.57 1 1 0 0 1 1 1V20a1 1 0 0 1-1 1A17 17 0 0 1 3 4a1 1 0 0 1 1-1h3.5a1 1 0 0 1 1 1c0 1.25.2 2.45.57 3.57a1 1 0 0 1-.25 1z" fill="#c3c9d2"/>
    </svg>
    <div class="ref-tag">Ref. 5009</div>

    <div class="hero photo-day" role="img" aria-label="Modern brick and glass office building with parked car"></div>
    <div class="hero-panel"></div>
    <h1 class="headline">Commercial<br>Leasing<br>Opportunity</h1>

    <h2 class="section-title">Highlights</h2>
    <ul class="highlights col-a">
      <li>Feugiat nisl at, sagittis diam</li>
      <li>Sed sed rhoncus nulla</li>
      <li>Id gravida elit.</li>
      <li>In hac habitasse platea dictumst.</li>
      <li>Aliquam in elit est.</li>
      <li>Sed sed rhoncus nulla</li>
      <li>Id gravida elit.</li>
    </ul>
    <ul class="highlights col-b">
      <li>Feugiat nisl at, sagittis diam</li>
      <li>Sed sed rhoncus nulla</li>
      <li>Id gravida elit.</li>
      <li>In hac habitasse platea dictumst.</li>
      <li>Aliquam in elit est.</li>
      <li>Sed sed rhoncus nulla</li>
      <li>Id gravida elit.</li>
    </ul>

    <div class="metric" style="top:820px">
      <svg class="metric-icon" width="40" height="40" viewBox="0 0 40 40" aria-hidden="true"><rect x="3" y="3" width="34" height="34" fill="none" stroke="#fff" stroke-width="3" stroke-dasharray="6 4"/></svg>
      <div class="metric-label">SITE SIZE</div>
      <div class="metric-value">2260 SF</div>
    </div>
    <div class="metric" style="top:972px">
      <svg class="metric-icon" width="40" height="40" viewBox="0 0 40 40" aria-hidden="true"><rect x="3" y="3" width="34" height="34" fill="none" stroke="#fff" stroke-width="3"/><path d="M3 20h34M20 3v34" stroke="#fff" stroke-width="3"/></svg>
      <div class="metric-label">LEASABLE AREA</div>
      <div class="metric-value">960 SF</div>
    </div>
    <div class="metric" style="top:1124px">
      <svg class="metric-icon" width="40" height="40" viewBox="0 0 40 40" aria-hidden="true"><rect x="3" y="3" width="34" height="34" rx="4" fill="#fff"/><path d="M15 30V10h7a6 6 0 0 1 0 12h-7" fill="none" stroke="#243f6c" stroke-width="4"/></svg>
      <div class="metric-label">PRIVATE</div>
      <div class="metric-value">PARKING</div>
    </div>

    <div class="gallery-main photo-night" role="img" aria-label="Office building lit up at dusk"></div>
    <div class="gallery-side photo-day" style="top:1200px" role="img" aria-label="Corner view of modern office building"></div>
    <div class="gallery-side photo-brick" style="top:1372px;height:148px" role="img" aria-label="Brick office building facade with parking"></div>

    <footer class="contact-band">
      <div class="contact-title">Contact Us</div>
      <div class="contact-card">
        <strong>Daniel Ashford</strong><br>
        Vice President &amp; Managing Director<br>
        C +1 555 010 4417 · T +1 555 010 2290<br>
        daniel.ashford@marlowcrest.com
      </div>
    </footer>
  </article>

</body>
</html>
```